We want to revamp our current website -www.kelvota-eng.com

We need to have a new website for our company that offers non-destructive and testing solutions around Africa. We have a current website but it does not fulfil our needs as it is:<br/>1. Not clear and bright<br/>2. Does not fit well in mobile <br/>3. Is not easily updatable by our staff. <br/>4. Is not linked to our social media sites.<br/>We would like to have a website that addresses the above issues. Our colours are Red and Blue and should communicate to our clients, that we are a professional company open for business, ready to solve their non-destructive testing problems around Africa. * Helpful if it is a wordpress website.

Target Market(s)

Our customers are B2B Corporate clients. We mainly work in
1. Storage Terminals
2. Refineries
3. Oil and Gas offshore and onshore rigs.

Industry/Entity Type

Oil And Gas

Contact Information for Business Card

Please find our current business card on the uploaded files.

Coding

Coded - Design and coding required

Number of Pages Required

5+ page

Font styles to use
Serif
Sans Serif

Requirements
Must have
• I like this site www.pirelo-inspection.com They are in the same industry.
• I don't understand how to call them but all the 'call to action' buttons, and links to our Social media pages.
• Must have a place where we update information in a regular basis. A Blog!

```html
<!DOCTYPE html>
<html lang="en">
<head>
<meta charset="utf-8">
<title>Kelvota Engineering</title>
<link href="https://fonts.googleapis.com/css2?family=Lato:wght@400;700;900&family=Raleway:wght@400;500;600;700&display=swap" rel="stylesheet">
<style>
:root{
  --navy:#1f2d66;
  --navy-dark:#17224f;
  --red:#b5141c;
  --red-dark:#8f0f16;
  --ink:#2a2f45;
  --muted:#8a8f9c;
  --line:#e3e5ea;
  --pale:#f1f3f7;
  --white:#ffffff;
}
*{box-sizing:border-box;margin:0;padding:0}
html,body{width:1200px;height:4713px;overflow:hidden}
body{position:relative;font-family:'Raleway',sans-serif;color:var(--ink);background:var(--white)}
.abs{position:absolute}
.brand{display:flex;align-items:center;gap:12px;font-family:'Lato',sans-serif;font-weight:700;color:var(--navy)}
.brand .dot{width:46px;height:46px;border-radius:50%;background:var(--red)}
.site-header{left:0;top:0;width:1200px;height:90px;border-top:3px solid var(--red);background:var(--white)}
.site-header .brand{position:absolute;left:102px;top:20px;font-size:23px}
.lang{position:absolute;left:574px;top:36px;font-size:14px;color:#666}
.call{position:absolute;left:732px;top:30px;font-size:14px;color:#444;display:flex;align-items:center;gap:10px}
.call b{font-size:19px;font-weight:500;color:#333}
.main-nav{left:0;top:90px;width:1200px;height:62px;background:linear-gradient(var(--navy),var(--navy-dark));display:flex;padding-left:76px}
.main-nav a{color:#fff;text-decoration:none;font-size:14px;font-weight:600;padding:0 25px;line-height:62px}
.main-nav a.active{background:#2b3d82}
.hero{left:0;top:152px;width:1200px;height:506px;background:linear-gradient(180deg,#6e7f97 0%,#3b4a66 45%,#1d2536 100%)}
.hero h1{position:absolute;left:120px;top:150px;font-family:'Lato',sans-serif;font-size:50px;font-weight:700;color:#fff}
.hero p{position:absolute;left:127px;top:225px;font-size:20px;color:#fff}
.btn{display:inline-flex;align-items:center;gap:14px;background:var(--red);color:#fff;font-size:14px;font-weight:600;border-radius:26px;padding:0 10px 0 22px;height:46px;text-decoration:none}
.btn i{width:30px;height:30px;border-radius:50%;background:rgba(255,255,255,.9)}
.hero .btn{position:absolute;left:253px;top:275px}
.dots{position:absolute;left:1124px;top:180px;display:flex;flex-direction:column;gap:14px}
.dots span{width:11px;height:11px;border-radius:50%;border:2px solid #fff}
.dots span:first-child{background:#fff}
.about-word{left:-30px;top:900px;font-family:'Lato',sans-serif;font-size:100px;font-weight:900;letter-spacing:14px;color:#eceef3;transform:rotate(-90deg);transform-origin:center;width:440px;height:120px;left:-150px;top:900px}
.photo{background:linear-gradient(135deg,#4d6b86,#a9b6bf 50%,#5a5344)}
.about-photo{left:148px;top:745px;width:452px;height:428px}
.play{position:absolute;left:176px;top:164px;width:100px;height:100px;border-radius:50%;background:rgba(255,255,255,.35);display:flex;align-items:center;justify-content:center}
.play span{width:74px;height:74px;border-radius:50%;background:#fff;display:flex;align-items:center;justify-content:center}
.panel{background:var(--navy);color:#fff}
.about-panel{left:600px;top:772px;width:476px;height:428px;padding:30px 40px}
.eyebrow{font-size:16px;letter-spacing:4px;font-weight:600}
.mini{width:36px;height:36px;border-radius:50%;background:var(--red);display:inline-block}
.about-panel h2{font-family:'Lato',sans-serif;font-size:29px;font-weight:700;margin:14px 0 22px}
.copy{font-size:14px;line-height:26px;text-align:justify}
.link{font-size:14px;font-weight:700;text-decoration:underline;color:inherit;display:inline-block;margin-top:26px}
.focus{left:0;top:1285px;width:1200px;height:733px;background:linear-gradient(180deg,#eef1f6,#f6f7fa)}
.sec-title{position:absolute;left:0;width:1200px;text-align:center}
.sec-title .eyebrow{color:var(--navy);font-size:16px}
.sec-title h2{font-family:'Lato',sans-serif;font-weight:500;font-size:34px;color:var(--navy);margin-top:10px;display:flex;justify-content:center;align-items:center;gap:14px}
.grid{position:absolute;left:110px;top:205px;width:978px;height:422px;display:grid;grid-template-columns:repeat(3,1fr);grid-template-rows:1fr 1fr;background:#fff;border:1px solid var(--line)}
.cell{position:relative;display:flex;flex-direction:column;align-items:center;justify-content:center;text-align:center;padding:0 30px}
.cell h3{font-size:16px;font-weight:600;color:var(--navy)}
.cell h3::after{content:"";display:block;width:32px;height:2px;background:var(--red);margin:10px auto 14px}
.cell p{font-size:13.5px;line-height:25px;color:var(--muted)}
.tile{background:linear-gradient(160deg,#4f79b4,#c9d6e6 60%,#7b8799)}
.tile.dark{background:linear-gradient(160deg,#4a5d92,#26336a)}
.ring{width:104px;height:104px;border-radius:50%;border:2px dashed rgba(255,255,255,.85)}
.notch{position:absolute;left:50%;top:0;margin-left:-12px;border:12px solid transparent;border-top-color:#fff}
.inspect-photo{left:600px;top:2018px;width:600px;height:554px;background:linear-gradient(135deg,#8b8b88,#5f4c3e 55%,#9aa0a4)}
.svc-panel{padding:36px 38px;outline:3px solid #fff;outline-offset:-10px}
.inspect-panel{left:118px;top:2120px;width:514px;height:348px}
.svc-panel h2{font-family:'Lato',sans-serif;font-size:29px;font-weight:700;display:flex;align-items:center;gap:14px;margin:14px 0 22px}
.svc-panel .copy{font-size:13.5px;line-height:26px}
.svc-panel .btn{margin-top:24px}
.eng-photo{left:0;top:2572px;width:600px;height:550px;background:linear-gradient(135deg,#4f8ab8,#c2733a 50%,#6c5b45)}
.eng-panel{left:560px;top:2672px;width:522px;height:350px}
.blog{left:0;top:3122px;width:1200px;height:613px;background:linear-gradient(180deg,#eef1f6 0,#eef1f6 490px,#fff 490px)}
.cards{position:absolute;left:110px;top:178px;width:978px;height:435px;display:grid;grid-template-columns:repeat(3,1fr);gap:10px}
.card{background:#fff;border:1px solid var(--line);padding:4px}
.card .img{height:192px}
.card .body{padding:18px 20px}
.date{font-size:11.5px;letter-spacing:2px;color:var(--red);font-weight:700}
.card h3{font-size:15.5px;font-weight:600;color:var(--navy);line-height:26px;margin:12px 0 8px}
.card p{font-size:13.5px;line-height:25px;color:var(--muted)}
.card .link{color:var(--red);font-size:13.5px;margin-top:12px}
.partners{left:110px;top:3775px;width:980px;display:grid;grid-template-columns:repeat(5,1fr);row-gap:40px}
.partner{height:80px;display:flex;align-items:center;justify-content:center;font-family:'Raleway',sans-serif;font-size:20px;font-weight:700;color:#9aa0ab}
.partner.on{background:#fff;box-shadow:0 2px 10px rgba(0,0,0,.12);color:#222;margin:0 22px}
.view-more{left:508px;top:4013px}
.map{left:0;top:4160px;width:400px;height:486px;background:linear-gradient(135deg,#eceff2,#dfe4e8)}
.pin{position:absolute;left:164px;top:196px}
.footer-panel{left:400px;top:4160px;width:400px;height:486px;text-align:center;padding-top:60px}
.footer-panel .dot-big{width:88px;height:88px;border-radius:50%;background:var(--red);margin:0 auto}
.footer-panel .name{font-size:17px;font-weight:600;margin-top:16px}
.info{font-size:13px;line-height:25px;margin-top:18px}
.info svg{display:block;margin:0 auto 6px}
.city{left:800px;top:4160px;width:400px;height:486px;background:linear-gradient(180deg,#9db6d2,#6f7f8e 50%,#4c5745)}
.bottom-bar{left:0;top:4646px;width:1200px;height:67px;background:var(--red);color:#fff}
.social{position:absolute;left:110px;top:18px;display:flex;gap:10px}
.social span{width:30px;height:30px;border-radius:50%;border:1.5px solid #fff}
.social span:nth-child(2){background:#fff}
.bottom-bar p{position:absolute;left:868px;top:24px;font-size:12px}
</style>
</head>
<body>

<header class="abs site-header">
  <div class="brand"><span class="dot"></span>Kelvota Engineering</div>
  <div class="lang">Eng ▾</div>
  <div class="call">
    <svg width="28" height="28" viewBox="0 0 24 24" fill="none" stroke="#b5141c" stroke-width="1.6"><path d="M5 3h4l2 5-3 2a11 11 0 0 0 6 6l2-3 5 2v4a2 2 0 0 1-2 2A17 17 0 0 1 3 5a2 2 0 0 1 2-2z"/></svg>
    <span>Call us Today : <b>+ 254 20 418 3920/1</b></span>
  </div>
</header>

<nav class="abs main-nav">
  <a class="active">Home</a><a>About Us</a><a>Inspection</a><a>NDT Services</a><a>Advanced NDT Services</a><a>Engineering Services</a><a>Contact Us</a>
</nav>

<section class="abs hero" role="img" aria-label="Oil storage terminal at dusk">
  <h1>Kelvota Engineering</h1>
  <p>We offer inspection &amp; engineering services</p>
  <a class="btn">GET STARTED <i></i></a>
  <div class="dots"><span></span><span></span><span></span><span></span></div>
</section>

<div class="abs about-word">ABOUT</div>
<div class="abs about-photo photo" role="img" aria-label="Pipeline on a mountain slope with workers">
  <div class="play"><span><svg width="20" height="20" viewBox="0 0 20 20"><path d="M6 3l11 7-11 7z" fill="#1f2d66"/></svg></span></div>
</div>
<section class="abs about-panel panel">
  <span class="mini"></span>
  <div class="eyebrow" style="margin-top:12px">ABOUT</div>
  <h2>KELVOTA ENGINEERING</h2>
  <p class="copy">With roots in Mombasa, we have over 15 years' experience in NDT, Mechanical engineering and Marine services. We enjoy a regional presence in The larger Eastern and Central African Region. Though our head office is located in Mombasa, Kenya, with a fully fledged testing laboratory not far from our office. We provide testing services across various countries in Africa.</p>
  <a class="link">LEARN MORE ⊕</a>
</section>

<section class="abs focus">
  <div class="sec-title" style="top:95px">
    <div class="eyebrow">WORK IN</div>
    <h2><span class="mini"></span>OUR FOCUS AREA</h2>
  </div>
  <div class="grid">
    <div class="cell tile" role="img" aria-label="Storage tank"><span class="ring"></span></div>
    <div class="cell"><h3>REFINERIES</h3><p>Lorem ipsum dolor sit amet, consectetur adipiscing elit, sed do eiusmod tempor incididunt ut labore et dolore</p></div>
    <div class="cell tile" role="img" aria-label="Offshore pipework"><span class="ring"></span></div>
    <div class="cell"><h3>STORAGE TERMINALS</h3><p>Lorem ipsum dolor sit amet, consectetur adipiscing elit, sed do eiusmod tempor incididunt ut labore et dolore</p></div>
    <div class="cell tile dark" role="img" aria-label="Refinery tanks"><span class="notch"></span><span class="ring"></span></div>
    <div class="cell"><h3>OIL AND GAS OFFSHORE</h3><p>Lorem ipsum dolor sit amet, consectetur adipiscing elit, sed do eiusmod tempor incididunt ut labore et dolore</p></div>
  </div>
</section>

<div class="abs inspect-photo" role="img" aria-label="Ultrasonic thickness gauge testing a pipe"></div>
<section class="abs inspect-panel panel svc-panel">
  <div class="eyebrow">SERVICES</div>
  <h2><span class="mini"></span>INSPECTION</h2>
  <p class="copy">Our Inspection team has the technical capability, backed by the right equipment to provide full range solutions in accordance with the client's requirement, and in compliance with local and international standards. We offer the following inspection services</p>
  <a class="btn">LEARN MORE <i></i></a>
</section>

<div class="abs eng-photo" role="img" aria-label="Technicians in orange coveralls working on steel structure"></div>
<section class="abs eng-panel panel svc-panel">
  <div class="eyebrow">SERVICES</div>
  <h2><span class="mini"></span>ENGINEERING SERVICES</h2>
  <p class="copy">Our Mechanical Engineering division is majorly involved with ASME compliant steel fabrication and welding both at our workshop and on client sites. With our corporate culture of quality, we have engaged a team of well-specialized technicians to carry on the fabrication operations.</p>
  <a class="btn">LEARN MORE <i></i></a>
</section>

<section class="abs blog">
  <div class="sec-title" style="top:82px">
    <div class="eyebrow">NEWS</div>
    <h2><span class="mini"></span>LATEST BLOG</h2>
  </div>
  <div class="cards">
    <article class="card"><div class="img photo" role="img" aria-label="Technician inspecting steel on site" style="background:linear-gradient(135deg,#6f8fb0,#c8783f 55%,#7b6a55)"></div><div class="body"><div class="date">JANUARY 23TH,2020</div><h3>Lorem ipsum dolor sit amet, conse ct etur adipiscing</h3><p>Lorem ipsum dolor sit amet, conse ctet ur adipiscing elit, sed do eiusmod tem por incididunt ut labore</p><a class="link">Learn more ⊕</a></div></article>
    <article class="card"><div class="img photo" role="img" aria-label="Team group outside the workshop" style="background:linear-gradient(135deg,#7f9a7c,#4f6a98 55%,#3c3c3c)"></div><div class="body"><div class="date">JANUARY 23TH,2020</div><h3>Lorem ipsum dolor sit amet, conse ct etur adipiscing</h3><p>Lorem ipsum dolor sit amet, conse ctet ur adipiscing elit, sed do eiusmod tem por incididunt ut labore</p><a class="link">Learn more ⊕</a></div></article>
    <article class="card"><div class="img photo" role="img" aria-label="Worker in safety vest testing a container" style="background:linear-gradient(135deg,#7a8f6a,#9a3a2c 55%,#5b4a3a)"></div><div class="body"><div class="date">JANUARY 23TH,2020</div><h3>Lorem ipsum dolor sit amet, conse ct etur adipiscing</h3><p>Lorem ipsum dolor sit amet, conse ctet ur adipiscing elit, sed do eiusmod tem por incididunt ut labore</p><a class="link">Learn more ⊕</a></div></article>
  </div>
</section>

<section class="abs partners">
  <div class="partner">Sandro Oil</div><div class="partner">Vexa</div><div class="partner on">Norvane</div><div class="partner">Tarnel</div><div class="partner">Coralis</div>
  <div class="partner">Brenmoor</div><div class="partner">Halvik Logistics</div><div class="partner">Petrova</div><div class="partner">Dunmark</div><div class="partner">Ostrel</div>
</section>
<a class="abs btn view-more">VIEW MORE <i></i></a>

<div class="abs map" role="img" aria-label="Street map of the office location in Mombasa">
  <svg class="pin" width="30" height="40" viewBox="0 0 30 40"><path d="M15 0a15 15 0 0 0-15 15c0 11 15 25 15 25s15-14 15-25A15 15 0 0 0 15 0z" fill="#d7141f"/><circle cx="15" cy="15" r="5" fill="#fff"/></svg>
</div>
<section class="abs footer-panel panel">
  <div class="dot-big"></div>
  <div class="name">Kelvota Engineering</div>
  <div class="info">
    <svg width="14" height="18" viewBox="0 0 30 40"><path d="M15 0a15 15 0 0 0-15 15c0 11 15 25 15 25s15-14 15-25A15 15 0 0 0 15 0z" fill="#e6a21c"/></svg>
    Nyali, Harbour Lane P.O. BOX 40512-80100<br>Mombasa Kenya
  </div>
  <div class="info">
    <svg width="16" height="16" viewBox="0 0 24 24"><path d="M5 3h4l2 5-3 2a11 11 0 0 0 6 6l2-3 5 2v4a2 2 0 0 1-2 2A17 17 0 0 1 3 5a2 2 0 0 1 2-2z" fill="#e6a21c"/></svg>
    + 254 20 418 3920/1
  </div>
  <div class="info">
    <svg width="18" height="14" viewBox="0 0 18 14"><rect width="18" height="14" rx="2" fill="#e6a21c"/><path d="M1 1l8 6 8-6" stroke="#1f2d66" fill="none" stroke-width="1.5"/></svg>
    info@kelvota-eng.com
  </div>
</section>
<div class="abs city" role="img" aria-label="Aerial view of the city skyline"></div>

<footer class="abs bottom-bar">
  <div class="social"><span></span><span></span><span></span><span></span></div>
  <p>© Copyrights 2020 | Kelvota Engineering</p>
</footer>

</body>
</html>
```